New Webpage for High Class Expert Witness Services Company

We are looking for a minimalist design for a webpage that just has our logo and an entry form offer to connect with one of our Liaisons.
The entry form should just ask for Name, Email, Contact Info and Description of Project.

Company Name is: The Marlowe Crest Advisory Services

Number of Pages Required

1 page

```html
<!DOCTYPE html>
<html lang="en">
<head>
<meta charset="UTF-8">
<title>The Marlowe Crest Advisory Services — Request Consultation</title>
<link href="https://fonts.googleapis.com/css2?family=Cinzel:wght@400;600;700&family=Outfit:wght@300;400;600&display=swap" rel="stylesheet">
<style>
  :root {
    --page-bg: #0e0e0e;
    --text-light: #f2f2f2;
    --text-soft: #dcdcdc;
    --accent-grey: #9c9c9c;
    --field-bg: #dcdcdc;
    --gold: #6b5530;
    --gold-text: #7d6534;
    --card-edge: rgba(255,255,255,0.16);
  }
  * { box-sizing: border-box; margin: 0; padding: 0; }
  html, body {
    width: 1200px; height: 675px; overflow: hidden;
    background: var(--page-bg);
    font-family: "Outfit", sans-serif;
    color: var(--text-light);
  }
  .page {
    position: relative; width: 1200px; height: 675px;
    background: radial-gradient(ellipse 260px 320px at 600px 420px, #1d1d1d 0%, var(--page-bg) 100%);
  }
  .brand {
    position: absolute; top: 40px; left: 0; width: 1200px;
    display: flex; justify-content: center; align-items: center; gap: 12px;
  }
  .brand-mark {
    width: 14px; height: 14px; border-radius: 50%;
    background: var(--text-soft);
  }
  .brand-name {
    font-family: "Cinzel", serif; font-weight: 400;
    font-size: 21px; letter-spacing: 1.5px; color: var(--text-soft);
  }
  .headline {
    position: absolute; top: 106px; left: 0; width: 1200px;
    text-align: center; font-family: "Cinzel", serif; font-weight: 400;
    font-size: 31px; line-height: 37px; letter-spacing: 2.5px;
    color: var(--text-light);
  }
  .headline strong { font-weight: 700; color: var(--accent-grey); }
  .tagline {
    position: absolute; top: 188px; left: 0; width: 1200px;
    text-align: center; font-weight: 300; font-size: 16px;
    letter-spacing: 1.3px; color: var(--text-soft);
  }
  .inquiry-card {
    position: absolute; left: 424px; top: 228px; width: 352px; height: 412px;
    border-radius: 23px; border: 1px solid var(--card-edge);
    background: radial-gradient(ellipse 200px 230px at 50% 48%, #4d4d4d 0%, #2a2a2a 55%, #1b1b1b 100%);
    box-shadow: 0 0 40px rgba(255,255,255,0.05);
  }
  .card-title {
    position: absolute; top: 248px; left: 0; width: 1200px;
    text-align: center; font-weight: 300; font-size: 22px; color: var(--text-light);
  }
  .card-title strong { font-weight: 600; color: #a8a8a8; }
  .card-rule {
    position: absolute; left: 515px; top: 288px; width: 171px; height: 1px;
    background: linear-gradient(90deg, transparent, #8a8a8a, transparent);
  }
  .field-label {
    position: absolute; left: 469px; font-size: 11px; font-weight: 400; color: var(--text-light);
  }
  .field-input {
    position: absolute; left: 469px; width: 263px; height: 34px;
    background: var(--field-bg); border: none; border-radius: 2px;
    font-family: "Outfit", sans-serif; font-size: 11px; padding: 0 10px;
  }
  textarea.field-input { height: 85px; padding: 8px 10px; resize: none; }
  .submit-button {
    position: absolute; left: 469px; top: 585px; width: 263px; height: 34px;
    background: var(--gold); border: none; border-radius: 2px;
    color: #fff; font-family: "Outfit", sans-serif; font-size: 11px;
  }
  .assurance {
    position: absolute; top: 636px; font-weight: 300; font-size: 16px; color: var(--text-soft);
  }
  .assurance strong { font-weight: 600; color: var(--gold-text); }
  .assurance-left { left: 120px; }
  .assurance-right { right: 148px; }
</style>
</head>
<body>
<main class="page">
  <header class="brand">
    <span class="brand-mark"></span>
    <span class="brand-name">The Marlowe Crest Advisory Services</span>
  </header>

  <h1 class="headline">When the stakes are <strong>absolute,</strong><br>the standard must be too.</h1>
  <p class="tagline">Expert witness integration &amp; legal defense support</p>

  <section class="inquiry-card" aria-label="Consultation request"></section>
  <h2 class="card-title">Tell us about Your <strong>Matter</strong></h2>
  <div class="card-rule"></div>

  <form class="inquiry-form">
    <label class="field-label" for="full-name" style="top:300px">Full Name</label>
    <input class="field-input" id="full-name" type="text" style="top:316px">

    <label class="field-label" for="email" style="top:358px">Email</label>
    <input class="field-input" id="email" type="email" style="top:374px">

    <label class="field-label" for="contact" style="top:415px">Contact Number</label>
    <input class="field-input" id="contact" type="tel" style="top:431px">

    <label class="field-label" for="description" style="top:473px">Description of Project</label>
    <textarea class="field-input" id="description" style="top:489px"></textarea>

    <button class="submit-button" type="submit">Request Consultation</button>
  </form>

  <p class="assurance assurance-left"><strong>24 hr</strong> Response guarantee</p>
  <p class="assurance assurance-right"><strong>100%</strong> Confidential</p>
</main>
</body>
</html>
```